FREE Network Assessment image for landing page

This graphic will be on a landing page and on the left will be Text and a download button that we change and control. The graphic for this project will be to the right.
I will add an example of the landing page area so that it makes more sense.

Please include the text from the sample - the font needs to be the same style as what we are using on the left side!

The graphic needs to be a .png file, roughly 713 x 527 white background. Use discretion on design layout.

Colors are black, Red = PMS 1795 and Gray = Cool Gray 10

Thanks,
Tom Garrick

Target Market(s)

small businesses

Industry/Entity Type

Information Technology

Font styles to use
Other font styles liked:
• See sample

Requirements
Must have
• see description
Nice to have
• Possibly small technology related image to help enhance the text but I don't want any image to compete with the text. Keep in mind the colors mentioned in the description - this is the web site colors.
Should not have
• Should not be hard to read

```html
<!DOCTYPE html>
<html lang="en">
<head>
<meta charset="utf-8">
<title>Free Network &amp; Computer Health Check Service</title>
<link rel="stylesheet" href="https://fonts.googleapis.com/css2?family=Oswald:wght@500;600&family=PT+Sans:wght@400;700&display=swap">
<style>
  :root {
    --red: #e2312f;
    --black: #0d0d0d;
    --gray: #5c5c60;
    --text: #3a3a3a;
    --white: #ffffff;
    --box-border: #9a9a9a;
    --art-light: #d9d9dc;
    --art-mid: #8c8c90;
    --art-dark: #3c3c40;
  }
  * { box-sizing: border-box; margin: 0; padding: 0; }
  html, body { width: 1200px; height: 887px; overflow: hidden; background: var(--white); }
  .card { position: relative; width: 1200px; height: 887px; background: var(--white); font-family: "PT Sans", Arial, sans-serif; }

  .headline { position: absolute; left: 0; top: 0; font-weight: inherit; }
  .headline-free {
    position: absolute; left: 34px; top: 8px;
    font-family: "Oswald", "Arial Narrow", sans-serif; font-weight: 600;
    font-size: 206px; line-height: 240px; color: var(--red); letter-spacing: 0;
  }
  .headline-line {
    position: absolute; left: 431px;
    font-family: "Oswald", "Arial Narrow", sans-serif; font-weight: 500;
    font-size: 80px; line-height: 96px; white-space: nowrap; letter-spacing: 5px;
  }
  .headline-line.top { top: 26px; color: var(--black); }
  .headline-line.bottom { top: 111px; color: var(--gray); }
  .headline-line .accent { color: var(--red); }

  .learn-title {
    position: absolute; left: 72px; top: 288px;
    font-size: 42px; font-weight: 700; color: var(--black); letter-spacing: 1.6px; line-height: 42px; white-space: nowrap;
  }

  .benefits { position: absolute; left: 72px; top: 358px; list-style: none; }
  .benefit { position: relative; height: 82.5px; padding-left: 61px; white-space: nowrap; }
  .benefit .tick { position: absolute; left: 4px; top: 6px; width: 24px; height: 24px; }
  .benefit-title { display: block; font-size: 31px; font-weight: 700; color: var(--gray); line-height: 32px; letter-spacing: .6px; }
  .benefit-detail { display: block; font-size: 25px; color: var(--text); line-height: 30px; letter-spacing: .4px; }

  .hero-art {
    position: absolute; left: 790px; top: 382px; width: 385px; height: 355px;
    border-radius: 24px;
    background: linear-gradient(160deg, var(--art-light) 0%, var(--art-mid) 50%, var(--art-dark) 100%);
  }

  .cta {
    position: absolute; left: 76px; top: 779px; width: 383px; height: 54px;
    background: var(--black); border-radius: 10px 8px 8px 10px;
    display: flex; align-items: center; padding-left: 10px; gap: 6px;
    color: var(--white); font-size: 23px; white-space: nowrap; text-decoration: none;
  }
  .cta svg { width: 48px; height: 36px; flex: none; }
  .cta strong { font-weight: 700; }
</style>
</head>
<body>
<div class="card">
  <h1 class="headline">
    <span class="headline-free">FREE</span>
    <span class="headline-line top">Network &amp; Computer</span>
    <span class="headline-line bottom">Health Check <span class="accent">Service</span></span>
  </h1>

  <h2 class="learn-title">HERE'S WHAT YOU WILL LEARN</h2>

  <ul class="benefits">
    <li class="benefit">
      <svg class="tick" viewBox="0 0 24 24"><rect x="1" y="5" width="17" height="17" fill="#fff" stroke="#9a9a9a" stroke-width="1.5"/><path d="M5 13 L10 18 L22 2" fill="none" stroke="#e2312f" stroke-width="3.5" stroke-linecap="round" stroke-linejoin="round"/></svg>
      <span class="benefit-title">Check your network’s security against</span>
      <span class="benefit-detail">hacker attacks, theft, ransomware, viruses, and more.</span>
    </li>
    <li class="benefit">
      <svg class="tick" viewBox="0 0 24 24"><rect x="1" y="5" width="17" height="17" fill="#fff" stroke="#9a9a9a" stroke-width="1.5"/><path d="M5 13 L10 18 L22 2" fill="none" stroke="#e2312f" stroke-width="3.5" stroke-linecap="round" stroke-linejoin="round"/></svg>
      <span class="benefit-title">See who and what</span>
      <span class="benefit-detail">has access to your network and data.</span>
    </li>
    <li class="benefit">
      <svg class="tick" viewBox="0 0 24 24"><rect x="1" y="5" width="17" height="17" fill="#fff" stroke="#9a9a9a" stroke-width="1.5"/><path d="M5 13 L10 18 L22 2" fill="none" stroke="#e2312f" stroke-width="3.5" stroke-linecap="round" stroke-linejoin="round"/></svg>
      <span class="benefit-title">Perform Speed Tests</span>
      <span class="benefit-detail">both network and Internet speed tests.</span>
    </li>
    <li class="benefit">
      <svg class="tick" viewBox="0 0 24 24"><rect x="1" y="5" width="17" height="17" fill="#fff" stroke="#9a9a9a" stroke-width="1.5"/><path d="M5 13 L10 18 L22 2" fill="none" stroke="#e2312f" stroke-width="3.5" stroke-linecap="round" stroke-linejoin="round"/></svg>
      <span class="benefit-title">Resolve PC slowness issues,</span>
      <span class="benefit-detail">security vulnerabilities and improper configurations.</span>
    </li>
    <li class="benefit">
      <svg class="tick" viewBox="0 0 24 24"><rect x="1" y="5" width="17" height="17" fill="#fff" stroke="#9a9a9a" stroke-width="1.5"/><path d="M5 13 L10 18 L22 2" fill="none" stroke="#e2312f" stroke-width="3.5" stroke-linecap="round" stroke-linejoin="round"/></svg>
      <span class="benefit-title">Validate your backups</span>
      <span class="benefit-detail">are working and recoverable in a timely fashion.</span>
    </li>
  </ul>

  <div class="hero-art" role="img" aria-label="Technology illustration: a globe circled by arrows in front of server towers"></div>

  <a class="cta" href="#">
    <svg viewBox="0 0 48 36"><rect x="0" y="0" width="48" height="36" rx="8" fill="#fff"/><path d="M22 6 L10 18 L22 30 M36 6 L24 18 L36 30" fill="none" stroke="#0d0d0d" stroke-width="6" stroke-linejoin="miter"/></svg>
    <span><strong>BOOK</strong> AN APPOINTMENT <strong>NOW!</strong></span>
  </a>
</div>
</body>
</html>
```